New Bicycle shop business card

Hi!
I'm looking for a business card for my new proffesional bike mechanics shop. This shop is only for fixing broken bikes and not selling bikes.
Peferbly a modern and sleek and modern design.
Colors: black, grey, red, white
Information:
Name: Rijwielwerkplaats Vanhoutte
Shop owner: Bart Vanhoutte & Marieke Segers
Website: www.rijwielwerkplaats-vanhoutte.be
Email: info@rijwielwerkplaats-vanhoutte.be
Phone number: +32471902368
Street adres: Kerkweg 46
9940 Bellebeke
Slogan/shop information: Herstellingen van alle merken.
Logo: see files.
Target Market(s)
People who seek a mechanic to fix or upgrade their bikes.
Contact Information for Business Card
Information:
Website: info@rijwielwerkplaats-vanhoutte.be
9940 Bellebeke
Logo: see files.

```html
<!DOCTYPE html>
<html lang="nl">
<head>
<meta charset="utf-8">
<title>Rijwielwerkplaats Vanhoutte – visitekaartje</title>
<link rel="stylesheet" href="https://fonts.googleapis.com/css2?family=Open+Sans:wght@400;600;700;800&display=swap">
<style>
  :root {
    --stage: #3a3b3d;
    --black: #070707;
    --white: #ffffff;
    --red: #e5202e;
    --grey: #8a8a8a;
    --grey-light: #b9b9b9;
    --ink: #1b1b1b;
  }
  * { box-sizing: border-box; margin: 0; padding: 0; }
  html, body { width: 1200px; height: 900px; overflow: hidden; }
  body {
    background: var(--stage);
    font-family: "Open Sans", Arial, sans-serif;
    position: relative;
  }
  .card {
    position: absolute;
    left: 290px;
    width: 620px;
    height: 354px;
    border-radius: 26px;
    overflow: hidden;
    box-shadow: 0 14px 30px rgba(0,0,0,.45);
  }
  .card--front { top: 70px; background: var(--black); color: var(--white); }
  .card--back  { top: 476px; background: var(--white); color: var(--ink); }

  .brand {
    display: flex;
    align-items: center;
    gap: 12px;
    font-weight: 800;
    letter-spacing: .04em;
    text-transform: uppercase;
  }
  .brand__dot {
    width: 22px; height: 22px;
    border-radius: 50%;
    background: var(--red);
    flex: none;
  }
  .card--front .brand {
    position: absolute;
    left: 0; right: 0; top: 140px;
    justify-content: center;
    font-size: 25px;
    color: var(--white);
  }
  .slogan {
    position: absolute;
    left: 0; right: 0; top: 250px;
    text-align: center;
    font-size: 13px;
    font-weight: 600;
    letter-spacing: .02em;
  }

  .card--back .brand {
    position: absolute;
    left: 40px; top: 150px;
    width: 230px;
    flex-direction: column;
    align-items: flex-start;
    gap: 10px;
    font-size: 19px;
    line-height: 1.15;
    color: var(--ink);
  }
  .divider {
    position: absolute;
    left: 292px; top: 70px;
    width: 1.5px; height: 150px;
    background: var(--red);
  }
  .details { position: absolute; left: 318px; top: 48px; width: 290px; }
  .details__label { color: var(--red); font-size: 13px; font-weight: 600; }
  .details__owners { color: var(--grey); font-size: 15px; font-weight: 700; margin-top: 1px; }
  .details__company { color: var(--red); font-size: 15px; font-weight: 800; margin-top: 10px; }
  .details__role { font-size: 11px; font-weight: 600; margin-top: 1px; }
  .contact { list-style: none; margin-top: 14px; }
  .contact li {
    display: flex; align-items: center; gap: 8px;
    font-size: 11.5px; color: var(--grey);
    line-height: 1.75;
  }
  .contact svg { width: 11px; height: 11px; fill: var(--red); flex: none; }
  .address {
    position: absolute; left: 318px; top: 238px;
    font-size: 12.5px; color: var(--grey);
    letter-spacing: .02em;
  }
  .wave { position: absolute; left: 0; bottom: 0; width: 620px; height: 120px; }
</style>
</head>
<body>

  <section class="card card--front" aria-label="Voorzijde visitekaartje">
    <div class="brand"><span class="brand__dot"></span>Rijwielwerkplaats Vanhoutte</div>
    <p class="slogan">Herstellingen van alle merken.</p>
  </section>

  <section class="card card--back" aria-label="Achterzijde visitekaartje">
    <div class="brand"><span class="brand__dot"></span>Rijwielwerkplaats Vanhoutte</div>
    <span class="divider"></span>

    <div class="details">
      <p class="details__label">Shop owner:</p>
      <p class="details__owners">Bart Vanhoutte &amp; Marieke Segers</p>
      <p class="details__company">Rijwielwerkplaats Vanhoutte</p>
      <p class="details__role">General Manager</p>
      <ul class="contact">
        <li><svg viewBox="0 0 24 24"><path d="M6.6 10.8a15.1 15.1 0 0 0 6.6 6.6l2.2-2.2c.3-.3.7-.4 1-.2 1.1.4 2.3.6 3.6.6.6 0 1 .4 1 1V20c0 .6-.4 1-1 1A17 17 0 0 1 3 4c0-.6.4-1 1-1h3.5c.6 0 1 .4 1 1 0 1.3.2 2.5.6 3.6.1.3 0 .7-.2 1z"/></svg>+32471902368</li>
        <li><svg viewBox="0 0 24 24"><path d="M2 5h20v14H2zm2 2v.5l8 5 8-5V7l-8 5z"/></svg>info@rijwielwerkplaats-vanhoutte.be</li>
        <li><svg viewBox="0 0 24 24"><circle cx="12" cy="12" r="10"/></svg>www.rijwielwerkplaats-vanhoutte.be</li>
      </ul>
    </div>

    <p class="address">Kerkweg 46 9940 Bellebeke</p>

    <svg class="wave" viewBox="0 0 620 120" preserveAspectRatio="none" aria-hidden="true">
      <path d="M0 80 C200 40 380 100 620 10 L620 120 L0 120 Z" fill="var(--grey-light)"/>
      <path d="M0 90 C200 52 380 110 620 22 L620 120 L0 120 Z" fill="var(--ink)"/>
      <path d="M0 96 C200 58 380 116 620 28 L620 120 L0 120 Z" fill="var(--red)"/>
    </svg>
  </section>

</body>
</html>
```